Brightarc Orthodontics appointment card design

I need appointment cards/ business cards made. Front will be Logo, name, title, email, phone number and location (5263 Walnut Hollow Pkwy, Ste 412, Concord, NC 28027) . the back should have an appointment card (name, time, date) and also 3 addresses listed with a check box so we can check to which location they are going.
Dale Fenwick Orthodontics
- 6735 Orchard Street, Ste 514, Harrisburg, NC 28075
- 3647 Ridgeway Drive NE, Ste 810, Concord, NC 28025
- 2917 Thornbury Corporate Drive, Ste 605, Charlotte, NC 28277
Business card can be horizontal or vertical in Design.
I need to be able to edit it to update and add new employees

Requirements
Must have
• Front:
• - Logo
• - Name & Title (able to be edited)
• - phone (704-555-0186) & Email (need to be able to edit)
• - Address: 5263 Walnut Hollow Pkwy, Ste 412
• Concord, NC 28027
• Back:
• Appointment Card design:
• - Name, time, Date
• - 3 locations w/ a check box so the patient knows where to go:
• Dale Fenwick Orthodontics
• - 6735 Orchard Street, Ste 514, Harrisburg, NC 28075
• - 3647 Ridgeway Drive NE, Ste 810, Concord, NC 28025
• - 2917 Thornbury Corporate Drive, Ste 605, Charlotte, NC 28277

```html
<!DOCTYPE html>
<html lang="en">
<head>
<meta charset="utf-8">
<title>Brightarc Orthodontics – Appointment &amp; Business Card</title>
<link href="https://fonts.googleapis.com/css2?family=Roboto:wght@400;500;700&display=swap" rel="stylesheet">
<style>
  :root {
    --brand-blue: #1479bd;
    --ink: #4a4a4a;
    --ink-soft: #666;
    --line: #333;
    --paper: #ffffff;
    --backdrop: #3b3b3d;
  }
  * { box-sizing: border-box; margin: 0; padding: 0; }
  html, body { width: 1200px; height: 1000px; overflow: hidden; }
  body {
    background: var(--backdrop);
    font-family: "Roboto", Arial, sans-serif;
    position: relative;
  }
  .card {
    position: absolute;
    left: 230px;
    width: 740px;
    height: 410px;
    background: var(--paper);
    border-radius: 28px;
    overflow: hidden;
  }
  .appointment-card { top: 60px; }
  .business-card { top: 520px; }

  /* Appointment (back) side */
  .appointment-card .top-band {
    position: absolute; top: 0; left: 0; right: 0; height: 16px;
    background: var(--brand-blue);
  }
  .appointment-title {
    position: absolute; left: 40px; top: 44px;
    color: var(--brand-blue); font-weight: 700; font-size: 22px;
  }
  .appointment-brand {
    position: absolute; right: 40px; top: 110px;
    color: var(--brand-blue); font-weight: 700; font-size: 24px;
    display: flex; align-items: center; gap: 8px;
    white-space: nowrap;
  }
  .appointment-brand .brand-dot {
    width: 14px; height: 14px; border-radius: 50%; background: var(--brand-blue);
  }
  .field {
    position: absolute; display: flex; align-items: flex-end;
    font-size: 14px; color: var(--ink-soft);
  }
  .field .rule { flex: 1; border-bottom: 1.5px solid var(--line); margin-left: 8px; height: 1px; }
  .field-name { left: 40px; top: 98px; width: 330px; }
  .field-date { left: 40px; top: 148px; width: 330px; }
  .field-time { left: 40px; top: 208px; width: 660px; }
  .field-time .rule-lead { width: 330px; border-bottom: 1.5px solid var(--line); margin-right: 10px; }
  .meridiem {
    position: absolute; top: 240px; right: 40px;
    display: flex; gap: 22px; font-size: 15px; color: var(--ink);
  }
  .check { display: inline-flex; align-items: center; gap: 6px; }
  .box {
    display: inline-block; width: 16px; height: 16px;
    border: 2px solid var(--brand-blue); border-radius: 2px;
  }
  .practice-name {
    position: absolute; left: 0; right: 0; top: 262px; text-align: center;
    font-size: 21px; color: var(--brand-blue); font-weight: 700;
  }
  .practice-name span { font-size: 17px; font-weight: 400; color: var(--ink); }
  .location {
    position: absolute; font-size: 14px; line-height: 1.35; color: var(--ink-soft);
    display: flex; flex-direction: column; align-items: center; text-align: center;
    white-space: nowrap;
  }
  .location .box { margin-bottom: 6px; }
  .location-harrisburg { left: 30px; top: 238px; }
  .location-concord { left: 250px; top: 300px; }
  .location-charlotte { right: 30px; top: 330px; }

  /* Business (front) side */
  .business-brand {
    position: absolute; left: 0; right: 0; top: 70px;
    display: flex; justify-content: center; align-items: center; gap: 14px;
    color: var(--brand-blue); font-weight: 700; font-size: 50px;
    white-space: nowrap;
  }
  .business-brand .brand-dot {
    width: 26px; height: 26px; border-radius: 50%; background: var(--brand-blue);
  }
  .person {
    position: absolute; left: 0; right: 0; top: 178px; text-align: center;
  }
  .person-name { color: var(--brand-blue); font-weight: 700; font-size: 28px; letter-spacing: 0.5px; }
  .person-title { color: var(--ink); font-size: 19px; margin-top: 2px; }
  .contact-band {
    position: absolute; left: 0; right: 0; bottom: 0; height: 150px;
    background: var(--brand-blue);
    display: flex; align-items: center; justify-content: center; gap: 26px;
    color: #fff;
  }
  .contact-address { text-align: right; font-size: 19px; line-height: 1.3; }
  .contact-divider { width: 2px; height: 60px; background: #fff; }
  .contact-lines { font-size: 19px; line-height: 1.4; }
  .contact-line { display: flex; align-items: center; gap: 8px; }
  .contact-line svg { width: 16px; height: 16px; fill: #fff; }
</style>
</head>
<body>

<section class="card appointment-card" aria-label="Appointment card">
  <div class="top-band"></div>
  <h2 class="appointment-title">Next Appointment</h2>
  <div class="appointment-brand"><span class="brand-dot"></span>Brightarc Orthodontics</div>

  <div class="field field-name">Name<span class="rule"></span></div>
  <div class="field field-date">Date<span class="rule"></span></div>
  <div class="field field-time"><span class="rule-lead"></span>Time<span class="rule"></span></div>

  <div class="meridiem">
    <span class="check"><span class="box"></span>AM</span>
    <span class="check"><span class="box"></span>PM</span>
  </div>

  <p class="practice-name">Dale Fenwick <span>Orthodontics</span></p>

  <div class="location location-harrisburg">
    <span class="box"></span>6735 Orchard Street, Ste 514,<br>Harrisburg, NC 28075
  </div>
  <div class="location location-concord">
    <span class="box"></span>3647 Ridgeway Drive NE, Ste 810,<br>Concord, NC 28025
  </div>
  <div class="location location-charlotte">
    <span class="box"></span>2917 Thornbury Corporate Drive,<br>Ste 605, Charlotte, NC 28277
  </div>
</section>

<section class="card business-card" aria-label="Business card">
  <div class="business-brand"><span class="brand-dot"></span>Brightarc Orthodontics</div>
  <div class="person">
    <p class="person-name">DALE FENWICK</p>
    <p class="person-title">Orthodontics</p>
  </div>
  <div class="contact-band">
    <p class="contact-address">5263 Walnut Hollow Pkwy,<br>Ste 412 - Concord, NC 28027</p>
    <span class="contact-divider"></span>
    <div class="contact-lines">
      <p class="contact-line">
        <svg viewBox="0 0 24 24" aria-hidden="true"><path d="M6.6 10.8a15.1 15.1 0 0 0 6.6 6.6l2.2-2.2a1 1 0 0 1 1-.25 11.4 11.4 0 0 0 3.6.57 1 1 0 0 1 1 1V20a1 1 0 0 1-1 1A17 17 0 0 1 3 4a1 1 0 0 1 1-1h3.5a1 1 0 0 1 1 1c0 1.25.2 2.450.57 3.6a1 1 0 0 1-.25 1z"/></svg>
        704-555-0186
      </p>
      <p class="contact-line">
        <svg viewBox="0 0 24 24" aria-hidden="true"><path d="M2 5h20v14H2zm2 2v.5l8 5 8-5V7zm0 2.8V17h16V9.8l-8 5z"/></svg>
        dfenwick@brightarcortho.com
      </p>
    </div>
  </div>
</section>

</body>
</html>
```